New website for salon services and wedding hair and makeup

I am a professional hairstylist and makeup artist in Charleston, SC. I have my own company where I see clients for cut and color and I also go on site for weddings. I have a current website that I would like to update and change the style. I would like to add a contact form, map, additional pages and be mobile friendly. It is important to me that it have a site map and can show up in searches. I will need to add photos to the site every so often and would like to continue to work with the designer. I have a logo that I am happy with and have attached the file however if you think a new logo would help the look of the site I am open to it. My current website is www.brightcombstudio-example.com, I would like to change the style and layout so it looks up to date. Here are some links to sites that I like the look of but I don't want to limit your creativity. http://willowlanefolio-example.com/ http://www.runwaylensworks-example.com http://miraventhol-example.com/. I have attached a few files for mock up purposes, please let me know if you would like more content. Thank you!

Target Market(s)

Women, Brides

Industry/Entity Type

Hair And Beauty

Number of Pages Required

1 page

Font styles to use
Sans Serif
Script

Requirements
Must have
• Contact form, Mobile friendly, sitemap
Nice to have
• I really like the look for the sites I have included on the project description guide.
Should not have
• Nothing overly girly.

```html
<!DOCTYPE html>
<html lang="en">
<head>
<meta charset="utf-8">
<title>Brightcomb Hair and Makeup</title>
<link href="https://fonts.googleapis.com/css2?family=Montserrat:wght@400;600;700&family=Open+Sans:wght@400;600&display=swap" rel="stylesheet">
<style>
:root{
  --teal:#1fa9a8;
  --ink:#3a3a3a;
  --muted:#8a8a8a;
  --line:#e2e2e2;
  --footer:#f4f4f4;
  --white:#ffffff;
  --fb:#3b5998;--tw:#2fb3e8;--rss:#f39a1e;--gp:#dc4a38;
  --skin:#e9cdb8;--hair-light:#d8b98f;--hair-dark:#8a6247;
}
*{margin:0;padding:0;box-sizing:border-box}
html,body{width:776px;height:1200px;overflow:hidden;background:var(--white)}
body{position:relative;font-family:"Open Sans",sans-serif;color:var(--ink)}
.abs{position:absolute}
/* header */
.brand{left:62px;top:22px;width:170px;height:64px;display:flex;align-items:center;gap:10px}
.brand-mark{width:34px;height:34px;border-radius:50%;background:#9ee0df}
.brand-name{font-family:"Montserrat",sans-serif;font-weight:600;font-size:20px;color:var(--teal)}
.follow{right:66px;top:40px;display:flex;align-items:center;gap:8px}
.follow-label{font-size:9px;letter-spacing:1px;color:var(--muted);margin-right:6px}
.dot{width:22px;height:22px;border-radius:50%}
/* nav */
.nav{left:0;top:103px;width:776px;height:32px;background:var(--teal)}
.nav-item{position:absolute;top:11px;font-family:"Montserrat",sans-serif;font-size:8px;color:var(--white);letter-spacing:.5px}
.search{position:absolute;left:543px;top:7px;width:168px;height:18px;background:var(--white);font-size:7px;color:#aaa;padding:4px 8px}
.search svg{position:absolute;right:6px;top:4px}
/* hero */
.hero{left:0;top:142px;width:776px;height:311px;
  background:
    radial-gradient(ellipse 120px 150px at 640px 150px, var(--skin) 0%, rgba(233,205,184,0) 100%),
    radial-gradient(ellipse 260px 220px at 560px 120px, rgba(216,185,143,.85) 0%, rgba(216,185,143,0) 100%),
    linear-gradient(90deg,#f3f3f3 0%,#ecebea 38%,#d9c8b6 62%,#cdb69e 80%,#e2d8cf 100%)}
.hero-title{left:65px;top:248px;font-family:"Montserrat",sans-serif;font-weight:700;font-size:20px;letter-spacing:1.5px;color:var(--teal)}
.hero-sub{left:65px;top:283px;font-size:8px;color:var(--ink)}
.btn{display:inline-block;background:var(--teal);color:var(--white);font-family:"Montserrat",sans-serif;font-size:8px;letter-spacing:.5px}
.hero-btn{left:65px;top:316px;width:108px;height:28px;line-height:28px;text-align:center}
.arrow{top:278px;width:24px;height:24px;border-radius:50%;background:rgba(120,120,120,.55)}
/* cards */
.card{background:var(--white);border:1px solid var(--line)}
.card-photo{position:absolute;left:0;top:0;width:100%}
.card-title{position:absolute;left:0;width:100%;text-align:center;font-family:"Montserrat",sans-serif;font-weight:600;font-size:9px;letter-spacing:.6px;color:var(--ink);line-height:13px}
.card-link{position:absolute;left:0;width:100%;text-align:center;font-size:6.5px;letter-spacing:1px;color:var(--muted)}
.card-rule{position:absolute;left:18px;right:18px;border-top:1px solid var(--line)}
.feature-panel{position:absolute;right:0;top:90px;width:172px;height:76px;background:rgba(255,255,255,.8)}
/* footer */
.footer{left:0;top:978px;width:776px;height:191px;background:var(--footer)}
.col{position:absolute;top:20px}
.col h4{font-family:"Montserrat",sans-serif;font-weight:700;font-size:8px;letter-spacing:.6px;color:var(--ink);margin-bottom:11px}
.col li{list-style:none;font-size:7px;color:var(--muted);line-height:14px}
.email{width:160px;height:22px;background:var(--white);border:1px solid var(--line);font-size:7px;color:#999;padding:6px 8px;position:relative}
.email svg{position:absolute;right:8px;top:8px}
.foot-dots{display:flex;gap:10px;margin-top:14px}
.foot-dots .dot{width:24px;height:24px}
.bottom{left:0;top:1169px;width:776px;height:31px;background:var(--teal);color:var(--white);font-size:7px}
.bottom p{text-align:center;line-height:31px}
.bottom .to-top{position:absolute;right:66px;top:0;line-height:31px}
</style>
</head>
<body>

<header>
  <div class="abs brand"><span class="brand-mark"></span><span class="brand-name">Brightcomb</span></div>
  <div class="abs follow">
    <span class="follow-label">FOLLOW US</span>
    <span class="dot" style="background:var(--fb)"></span>
    <span class="dot" style="background:var(--tw)"></span>
    <span class="dot" style="background:var(--rss)"></span>
    <span class="dot" style="background:var(--gp)"></span>
  </div>
</header>

<nav class="abs nav">
  <span class="nav-item" style="left:65px">HOME</span>
  <span class="nav-item" style="left:147px">ABOUT</span>
  <span class="nav-item" style="left:233px">SERVICES</span>
  <span class="nav-item" style="left:323px">GALLERY</span>
  <span class="nav-item" style="left:414px">CONTACT</span>
  <div class="search">Search entire site here
    <svg width="9" height="9" viewBox="0 0 10 10"><circle cx="4" cy="4" r="3" fill="none" stroke="#555" stroke-width="1.3"/><line x1="6.2" y1="6.2" x2="9" y2="9" stroke="#555" stroke-width="1.4"/></svg>
  </div>
</nav>

<section>
  <div class="abs hero" role="img" aria-label="Portrait of a woman with long flowing blonde hair"></div>
  <h1 class="abs hero-title">A MOMENT TO LAST FOREVER</h1>
  <p class="abs hero-sub">Celebrate unforgettable wedding moments</p>
  <span class="abs btn hero-btn">DISCOVER MORE</span>
  <svg class="abs arrow" style="left:10px" viewBox="0 0 24 24"><path d="M14 7l-5 5 5 5" fill="none" stroke="#fff" stroke-width="2"/></svg>
  <svg class="abs arrow" style="left:742px" viewBox="0 0 24 24"><path d="M10 7l5 5-5 5" fill="none" stroke="#fff" stroke-width="2"/></svg>
</section>

<main>
  <article class="abs card" style="left:65px;top:525px;width:189px;height:207px">
    <div class="card-photo" style="height:140px;background:radial-gradient(ellipse 70px 60px at 130px 60px,#e6c7ae,rgba(230,199,174,0)),linear-gradient(135deg,#f1ece7 0%,#dcc9b6 60%,#b89a7f 100%)" role="img" aria-label="Makeup artist applying makeup to a bride"></div>
    <h3 class="card-title" style="top:148px">NEMO ENIM IPSAM<br>VOLUPTATEM</h3>
    <div class="card-rule" style="top:180px"></div>
    <span class="card-link" style="top:188px">DISCOVER MORE</span>
  </article>

  <article class="abs card" style="left:266px;top:525px;width:445px;height:207px;overflow:hidden">
    <div class="card-photo" style="height:207px;background:radial-gradient(ellipse 90px 90px at 120px 110px,#ecd3bf,rgba(236,211,191,0)),radial-gradient(ellipse 140px 80px at 110px 40px,rgba(206,170,118,.9),rgba(206,170,118,0)),linear-gradient(90deg,#f4f1ee,#e3d5c7 45%,#f2eeea 70%,#dfe9ea 100%)" role="img" aria-label="Bride with an elegant updo and veil"></div>
    <div class="feature-panel"></div>
    <h3 class="card-title" style="top:104px;left:auto;right:0;width:172px">NEMO ENIM IPSAM<br>VOLUPTATEM</h3>
    <span class="card-link" style="top:142px;left:auto;right:0;width:172px">DISCOVER MORE</span>
  </article>

  <article class="abs card" style="left:65px;top:745px;width:189px;height:212px">
    <div class="card-photo" style="height:135px;background:radial-gradient(ellipse 60px 55px at 80px 70px,#edd3c1,rgba(237,211,193,0)),linear-gradient(135deg,#efe6df 0%,#a57b5c 55%,#6e4a33 100%)" role="img" aria-label="Woman with soft brown curls"></div>
    <h3 class="card-title" style="top:152px">VOLUPTATEM SEQUI</h3>
    <div class="card-rule" style="top:180px"></div>
    <span class="card-link" style="top:190px">DISCOVER MORE</span>
  </article>

  <article class="abs card" style="left:266px;top:745px;width:218px;height:212px">
    <div class="card-photo" style="height:135px;background:radial-gradient(ellipse 55px 55px at 110px 80px,#f0d8c4,rgba(240,216,196,0)),radial-gradient(ellipse 100px 60px at 110px 30px,rgba(201,160,110,.9),rgba(201,160,110,0)),linear-gradient(135deg,#c9a57f,#e7d5c0 60%,#b98f68)" role="img" aria-label="Smiling bride with a braided hairstyle"></div>
    <h3 class="card-title" style="top:152px">CONSEQUUNTUR MAGNI</h3>
    <div class="card-rule" style="top:180px"></div>
    <span class="card-link" style="top:190px">DISCOVER MORE</span>
  </article>

  <article class="abs card" style="left:497px;top:745px;width:214px;height:212px">
    <div class="card-photo" style="height:135px;background:radial-gradient(ellipse 55px 55px at 150px 70px,#edd2be,rgba(237,210,190,0)),radial-gradient(ellipse 120px 70px at 100px 50px,rgba(214,186,140,.85),rgba(214,186,140,0)),linear-gradient(135deg,#f4f0ec,#e0cdbb 60%,#c8a98c)" role="img" aria-label="Woman with windswept blonde hair"></div>
    <h3 class="card-title" style="top:152px">VOLUPTATEM SEQUI NESCIUNT</h3>
    <div class="card-rule" style="top:180px"></div>
    <span class="card-link" style="top:190px">DISCOVER MORE</span>
  </article>
</main>

<footer class="abs footer">
  <div class="col" style="left:65px">
    <h4>QUICK LINKS</h4>
    <ul><li>Home</li><li>About Us</li><li>Who We Are</li><li>Our Services</li><li>Contact Us</li><li>Other Service</li></ul>
  </div>
  <div class="col" style="left:225px">
    <h4>INFORMATION</h4>
    <ul><li>Corporate Info</li><li>Contact Form</li><li>Our Location</li><li>FAQs</li><li>News</li><li>Blog</li></ul>
  </div>
  <div class="col" style="left:388px">
    <h4>MY ACCOUNT</h4>
    <ul><li>Products</li><li>Service Booking</li><li>Catalog</li><li>Prices</li><li>Service Offerings</li></ul>
  </div>
  <div class="col" style="left:551px">
    <h4>NEWSLETTER SIGN UP</h4>
    <div class="email">Enter your Email
      <svg width="7" height="5" viewBox="0 0 7 5"><path d="M0 0h7L3.5 5z" fill="#888"/></svg>
    </div>
    <h4 style="margin-top:18px">FOLLOW US</h4>
    <div class="foot-dots">
      <span class="dot" style="background:var(--fb)"></span>
      <span class="dot" style="background:var(--tw)"></span>
      <span class="dot" style="background:var(--rss)"></span>
      <span class="dot" style="background:var(--gp)"></span>
    </div>
  </div>
</footer>

<div class="abs bottom">
  <p>Brightcomb Hair and Makeup © 2015 - Privacy Policy</p>
  <span class="to-top">TOP</span>
</div>

</body>
</html>
```